1876 Basins & Spouts Business Card

I'm wanting to get a business card designed. Our business is 1876 Basins & Spouts
Details for the card:

1876 Basins & Spouts
Name: Harold Vesk
Email: harold@1876basinsandspouts.com.au
Website: www.1876basinsandspouts.com.au
Mobile: 0438 260 947
Phone: 02 7481 3926

Font of Basins & Spouts is called Snell Roundhand. Not sue what font logo text is.

I'm thinking two sided but it doesn't have to be.

```html
<!DOCTYPE html>
<html lang="en">
<head>
<meta charset="utf-8">
<title>1876 Basins &amp; Spouts – Business Card</title>
<link href="https://fonts.googleapis.com/css2?family=Roboto:wght@400;500&family=Open+Sans:wght@400&family=Poppins:wght@400&display=swap" rel="stylesheet">
<style>
  :root {
    --backdrop: #e4e4e4;
    --card: #ffffff;
    --ink: #111111;
    --ink-soft: #333333;
    --line: #cfcfcf;
  }
  * { margin: 0; padding: 0; box-sizing: border-box; }
  html, body { width: 1200px; height: 1200px; overflow: hidden; }
  body { background: var(--backdrop); position: relative; font-family: "Roboto", Arial, sans-serif; color: var(--ink); }

  .card {
    position: absolute;
    left: 262px;
    width: 686px;
    height: 392px;
    background: var(--card);
    border: 1px solid var(--line);
  }
  .card--front { top: 165px; }
  .card--back { top: 653px; }

  /* Front */
  .brand-mark {
    position: absolute;
    top: 62px;
    right: 46px;
    display: flex;
    align-items: center;
    gap: 8px;
    font-weight: 500;
    font-size: 15px;
    color: var(--ink);
  }
  .brand-mark__dot {
    width: 12px; height: 12px; border-radius: 50%;
    background: var(--ink);
  }
  .holder-name {
    position: absolute;
    left: 47px;
    top: 215px;
    font-size: 24px;
    line-height: 30px;
    font-weight: 500;
  }
  .contact-list {
    position: absolute;
    left: 48px;
    top: 269px;
    list-style: none;
    font-size: 16px;
    line-height: 22px;
    color: var(--ink-soft);
  }

  /* Back */
  .brand-lockup {
    position: absolute;
    left: 0; right: 0;
    top: 170px;
    display: flex;
    justify-content: center;
    align-items: center;
    gap: 12px;
    font-weight: 500;
    font-size: 30px;
    line-height: 38px;
    color: var(--ink);
  }
  .brand-lockup__dot {
    width: 20px; height: 20px; border-radius: 50%;
    background: var(--ink);
  }
  .tagline {
    position: absolute;
    left: 0; right: 0;
    top: 219px;
    text-align: center;
    font-family: "Open Sans", Arial, sans-serif;
    font-size: 11px;
    color: var(--ink-soft);
  }
  .web-address {
    position: absolute;
    left: 0; right: 0;
    top: 322px;
    text-align: center;
    font-family: "Poppins", Arial, sans-serif;
    font-size: 15px;
    letter-spacing: 2.6px;
    color: var(--ink);
  }
</style>
</head>
<body>
  <section class="card card--front" aria-label="Card front">
    <div class="brand-mark"><span class="brand-mark__dot"></span>1876 Basins &amp; Spouts</div>
    <h1 class="holder-name">Harold Vesk</h1>
    <ul class="contact-list">
      <li>P: 02 7481 3926</li>
      <li>M: 0438 260 947</li>
      <li>harold@1876basinsandspouts.com.au</li>
      <li>www.1876basinsandspouts.com.au</li>
    </ul>
  </section>

  <section class="card card--back" aria-label="Card back">
    <div class="brand-lockup"><span class="brand-lockup__dot"></span>1876 Basins &amp; Spouts</div>
    <p class="tagline">Heritage style shaped for the way you live today</p>
    <p class="web-address">www.1876basinsandspouts.com.au</p>
  </section>
</body>
</html>
```